Brindle Recycling needs a new web design

We need a new web design for our company based in Austin, TX. We resell and recycling electronics such as laptops, computer components, Zelvotabs, Quorns, etc. Since our inception over ten years ago, we’ve become one of the premier electronics recycling and remarketing companies in Austin, Texas.

```html
<!DOCTYPE html>
<html lang="en">
<head>
<meta charset="utf-8">
<title>Brindle Recycling – Computer Recycling Made Easy</title>
<link rel="stylesheet" href="https://fonts.googleapis.com/css2?family=Raleway:wght@300;400;500;600&display=swap">
<style>
  :root {
    --brand-blue: #1a6fd6;
    --hero-top: #1786f2;
    --hero-bottom: #46c9f6;
    --ink: #1c2430;
    --nav-ink: #38404c;
    --muted: #4a525c;
    --white: #ffffff;
    --accent-green: #4fe394;
    --art-light: #cfeede;
    --art-mid: #8fd46a;
    --art-dark: #49b451;
  }
  * { box-sizing: border-box; margin: 0; padding: 0; }
  html, body { width: 1200px; height: 634px; overflow: hidden; background: var(--white); }
  body { font-family: "Raleway", Arial, sans-serif; color: var(--ink); position: relative; }

  .site-header {
    height: 60px; display: flex; align-items: center; justify-content: space-between;
    padding: 0 46px; background: var(--white);
  }
  .brand { display: flex; align-items: center; gap: 10px; }
  .brand-dot { width: 28px; height: 28px; border-radius: 50%; background: var(--brand-blue); }
  .brand-name { font-size: 22px; font-weight: 600; color: var(--brand-blue); }

  .main-nav { display: flex; align-items: center; gap: 42px; font-size: 14px; color: var(--nav-ink); }
  .nav-item { display: flex; align-items: center; gap: 6px; }
  .nav-item svg { width: 9px; height: 6px; }

  .hero {
    position: relative; height: 420px;
    background: linear-gradient(180deg, var(--hero-top) 0%, var(--hero-bottom) 100%);
    color: var(--white);
  }
  .hero-copy { position: absolute; left: 47px; top: 38px; width: 545px; }
  .hero-title { font-size: 42px; font-weight: 300; line-height: 1.22; }
  .hero-text { margin-top: 22px; font-size: 15px; line-height: 1.75; font-weight: 400; }
  .hero-cta {
    display: inline-block; margin-top: 24px; padding: 7px 18px;
    border: 1.5px solid var(--white); border-radius: 3px;
    font-size: 15px; color: var(--white);
  }
  .hero-illustration {
    position: absolute; left: 830px; top: 78px; width: 312px; height: 250px;
    border-radius: 10px;
    background: linear-gradient(180deg, var(--art-light) 0%, var(--art-mid) 55%, var(--art-dark) 100%);
  }
  .scroll-down {
    position: absolute; left: 50%; bottom: -22px; transform: translateX(-50%);
    width: 44px; height: 44px; border-radius: 50%; background: var(--accent-green);
    display: flex; align-items: center; justify-content: center;
  }

  .services-intro { text-align: center; padding-top: 54px; }
  .services-title { font-size: 36px; font-weight: 400; color: var(--ink); line-height: 1.2; }
  .services-title .highlight { color: var(--brand-blue); }
  .services-sub { margin-top: 10px; font-size: 16px; color: var(--muted); }
</style>
</head>
<body>
  <header class="site-header">
    <div class="brand">
      <span class="brand-dot"></span>
      <span class="brand-name">Brindle Recycling</span>
    </div>
    <nav class="main-nav">
      <span class="nav-item">Services <svg viewBox="0 0 9 6"><path d="M1 1l3.5 3.5L8 1" fill="none" stroke="currentColor" stroke-width="1.2"/></svg></span>
      <span class="nav-item">Company <svg viewBox="0 0 9 6"><path d="M1 1l3.5 3.5L8 1" fill="none" stroke="currentColor" stroke-width="1.2"/></svg></span>
      <span class="nav-item">Hauling <svg viewBox="0 0 9 6"><path d="M1 1l3.5 3.5L8 1" fill="none" stroke="currentColor" stroke-width="1.2"/></svg></span>
      <span class="nav-item">FAQs</span>
      <span class="nav-item">Contact Us</span>
    </nav>
  </header>

  <section class="hero">
    <div class="hero-copy">
      <h1 class="hero-title">Computer Recycling<br>Made Easy</h1>
      <p class="hero-text">Want to make a difference to our environment and planet? Brindle Recycling is here to help! Brindle recycling has been helping keep the environment healthy since 2006, we specialize in recycling services that help citizens become experts at reducing waste. We have a passion to keep our world clean and are here to guide you through all the stages of the recycling process.</p>
      <span class="hero-cta">Talk To Us</span>
    </div>
    <div class="hero-illustration" role="img" aria-label="Illustration of a green globe with houses, trees, mountains and wind turbines"></div>
    <div class="scroll-down">
      <svg width="16" height="14" viewBox="0 0 16 14"><path d="M2 2l6 5 6-5M2 7l6 5 6-5" fill="none" stroke="#ffffff" stroke-width="1.6"/></svg>
    </div>
  </section>

  <section class="services-intro">
    <h2 class="services-title">Our <span class="highlight">Services</span></h2>
    <p class="services-sub">Our set of services includes so much to offer</p>
  </section>
</body>
</html>
```